Business Card for a Dental Office

The design should communicate integrity, quality and reliability. We also want the card look elegant, simple, but still stand out, different from the traditional-dental-office business card.

Industry/Entity Type

Business

```html
<!DOCTYPE html>
<html lang="en">
<head>
<meta charset="utf-8">
<title>Harlow Dental Studio – Business Card</title>
<link rel="stylesheet" href="https://fonts.googleapis.com/css2?family=Oswald:wght@500;600&family=Arimo:wght@400;700&display=swap">
<style>
  :root {
    --bg: #3a3a3c;
    --card-white: #ffffff;
    --card-black: #0d0d0d;
    --gold: #d4b028;
    --gold-soft: #c9a227;
    --ink: #1a1a1a;
    --grey: #5c5c5c;
    --text-light: #f2f2f2;
  }
  * { margin: 0; padding: 0; box-sizing: border-box; }
  html, body { width: 1200px; height: 950px; overflow: hidden; }
  body {
    background: var(--bg);
    position: relative;
    font-family: "Arimo", Arial, sans-serif;
  }
  .card {
    position: absolute;
    left: 230px;
    width: 740px;
    height: 423px;
    background: var(--card-white);
    overflow: hidden;
  }
  .card--back { top: 40px; }
  .card--front { top: 487px; }

  /* Back face */
  .back-brand {
    position: absolute;
    left: 0; right: 0; top: 150px;
    display: flex; align-items: center; justify-content: center; gap: 14px;
  }
  .brand-mark {
    width: 30px; height: 30px; background: var(--gold); display: block;
  }
  .brand-name {
    font-family: "Oswald", "Arial Narrow", sans-serif;
    font-weight: 600;
    color: var(--ink);
    text-transform: uppercase;
    letter-spacing: 1px;
    font-size: 34px;
    line-height: 1;
  }
  .back-web {
    position: absolute; left: 0; right: 0; top: 232px;
    text-align: center;
    font-size: 15px; letter-spacing: 4px; color: var(--grey);
  }

  /* Front face */
  .front-bg { position: absolute; inset: 0; }
  .front-brand {
    position: absolute; left: 470px; top: 52px;
  }
  .front-brand .brand-row { display: flex; align-items: center; gap: 9px; }
  .front-brand .brand-mark { width: 20px; height: 20px; }
  .front-brand .brand-name { font-size: 24px; }
  .tagline {
    margin: 5px 0 0 29px;
    font-size: 9.5px; letter-spacing: 1.2px; text-transform: uppercase;
    color: var(--gold-soft); font-weight: 700;
  }
  .holder { position: absolute; left: 58px; top: 72px; }
  .holder-name {
    font-family: "Oswald", "Arial Narrow", sans-serif;
    font-weight: 500; font-size: 24px; color: var(--gold);
    text-transform: uppercase; letter-spacing: 0.5px; line-height: 1.1;
  }
  .holder-role {
    font-weight: 700; font-size: 14px; color: var(--text-light);
    text-transform: uppercase; letter-spacing: 0.5px; margin-top: 3px;
  }
  .address {
    position: absolute; left: 58px; top: 205px;
    color: var(--text-light); font-size: 17px; line-height: 1.25;
  }
  .contacts {
    position: absolute; left: 58px; top: 252px;
    list-style: none; color: var(--text-light); font-size: 17px;
  }
  .contacts li { display: flex; align-items: center; gap: 9px; height: 23px; }
  .contacts svg { width: 15px; height: 15px; flex: none; }
</style>
</head>
<body>

<section class="card card--back" aria-label="Card back">
  <div class="back-brand">
    <span class="brand-mark" aria-hidden="true"></span>
    <span class="brand-name">Harlow Dental Studio</span>
  </div>
  <p class="back-web">www.harlowdental.com</p>
</section>

<section class="card card--front" aria-label="Card front">
  <svg class="front-bg" viewBox="0 0 740 423" preserveAspectRatio="none" aria-hidden="true">
    <path d="M0 0 H300 C345 0 352 70 390 140 C430 215 470 300 560 355 C620 392 690 405 740 410 V423 H0 Z" fill="var(--card-black)"/>
    <path d="M318 0 C360 10 370 80 405 145 C445 220 490 300 575 345 C630 375 690 392 740 398" fill="none" stroke="var(--gold)" stroke-width="4"/>
  </svg>

  <div class="front-brand">
    <div class="brand-row">
      <span class="brand-mark" aria-hidden="true"></span>
      <span class="brand-name">Harlow Dental Studio</span>
    </div>
    <p class="tagline">Your smile is our gift to others</p>
  </div>

  <div class="holder">
    <p class="holder-name">Mara Ellison</p>
    <p class="holder-role">President</p>
  </div>

  <p class="address">2710 Larkspur Avenue<br>Cedar Hollow, NY 10990</p>

  <ul class="contacts">
    <li>
      <svg viewBox="0 0 16 16" aria-hidden="true"><path d="M3 6c0-2 2-3 5-3s5 1 5 3l-2 1-1-2H6L5 7z M4 9h8l1 4H3z" fill="var(--gold)"/></svg>
      555 0142 7781
    </li>
    <li>
      <svg viewBox="0 0 16 16" aria-hidden="true"><rect x="4" y="1" width="8" height="14" rx="1.5" fill="var(--gold)"/><rect x="5.5" y="3" width="5" height="8" fill="var(--card-black)"/></svg>
      555 0198 3316
    </li>
    <li>
      <svg viewBox="0 0 16 16" aria-hidden="true"><rect x="4" y="1" width="8" height="5" fill="var(--gold)"/><rect x="1" y="6" width="14" height="6" rx="1" fill="var(--gold)"/><rect x="4" y="10" width="8" height="5" fill="var(--gold)" stroke="var(--card-black)"/></svg>
      555 0163 9024
    </li>
    <li>
      <svg viewBox="0 0 16 16" aria-hidden="true"><rect x="1" y="3" width="14" height="10" fill="var(--gold)"/><path d="M1 3l7 6 7-6" fill="none" stroke="var(--card-black)" stroke-width="1.3"/></svg>
      mara@harlowdental.com
    </li>
    <li>
      <svg viewBox="0 0 16 16" aria-hidden="true"><circle cx="8" cy="8" r="7" fill="var(--gold)"/><path d="M1 8h14M8 1c-3 3-3 11 0 14M8 1c3 3 3 11 0 14" fill="none" stroke="var(--card-black)" stroke-width="1"/></svg>
      www.harlowdental.com
    </li>
  </ul>
</section>

</body>
</html>
```